Step Forth Daily newsletter - Mail Chimp

Step Forth Daily - Empowering Life Coach needs Mail Chimp Newsletter Template. This is a newsletter I will send out monthly to current clients and prospective clients to offer (hopefully) inspiring and uplifting content AND to give info and dates of my upcoming workshops and retreats.

I have attached a word document with all of the different sections of the mail chimp template I would like to have - and hte actual content for the first newsletter.

I'd like to look uplifting, fun, inspiring.

I also need it to be easy for me to use to update in the future :)

Target Market(s)

Women - moms

Industry/Entity Type

Life Coaching

Requirements
Nice to have
• Color theme to match my "Step Forth Daily" logo

```html
<!DOCTYPE html>
<html lang="en">
<head>
<meta charset="utf-8">
<title>Step Forth Daily – Newsletter</title>
<link rel="stylesheet" href="https://fonts.googleapis.com/css2?family=Merriweather:ital,wght@0,400;0,700;1,400;1,700&family=Open+Sans:wght@600;700&display=swap">
<style>
:root{
  --purple:#5b2d8e;
  --indigo:#3b2e86;
  --blue:#27a8e0;
  --green:#8cc63f;
  --pink:#d4145a;
  --orange:#f7941d;
  --yellow:#fcd116;
  --ink:#231f20;
  --paper:#ffffff;
}
*{box-sizing:border-box;margin:0;padding:0}
html,body{width:1200px;height:3261px;overflow:hidden;background:var(--paper)}
body{position:relative;font-family:"Merriweather",Georgia,serif;color:var(--ink);font-size:19px;line-height:1.5}
.block{position:absolute;left:48px;right:48px}
p{margin-bottom:18px}

.brand{top:70px;left:48px;display:flex;align-items:center;gap:20px}
.brand-dot{width:46px;height:46px;border-radius:50%;background:var(--orange)}
.brand-name{font-family:"Merriweather",Georgia,serif;font-weight:700;font-size:64px;color:var(--purple);line-height:1}

.intro{top:318px}
.intro strong{font-weight:700}
.signoff{top:760px}
.signoff .name{font-style:italic;font-weight:700;color:var(--blue);font-size:26px;margin-top:8px}
.portrait{position:absolute;top:752px;left:900px;width:230px;height:150px;border-radius:50%;
  background:radial-gradient(circle at 50% 45%,#f2c79a 0 28%,#45b5e6 30% 70%,transparent 72%)}

.rule{position:absolute;left:48px;right:48px;height:4px;display:flex}
.rule span{flex:1}
.rule span:nth-child(1){background:var(--pink)}
.rule span:nth-child(2){background:var(--purple)}
.rule span:nth-child(3){background:var(--green)}
.rule span:nth-child(4){background:var(--orange)}

.tips-banner{position:absolute;top:1072px;left:305px;width:590px;height:78px;border-radius:14px;
  background:linear-gradient(90deg,#6fd0f2,#27a8e0 40%,#5b8fd6 75%,#6a3fa0);
  display:flex;align-items:center;justify-content:center}
.tips-banner span{font-family:"Open Sans",Arial,sans-serif;font-weight:700;font-size:30px;color:#fff200}

.happiness{top:1192px;right:340px}
.section-title{font-family:"Open Sans",Arial,sans-serif;font-weight:700;color:var(--blue);font-size:30px;margin-bottom:20px}
.arrows{list-style:none}
.arrows li{color:var(--purple);font-style:italic;font-weight:700;margin-bottom:8px;display:flex;align-items:center;gap:14px}
.arrows svg{flex:none}
.sunset{position:absolute;top:1162px;left:888px;width:270px;height:420px;border-radius:120px 120px 110px 110px;
  background:linear-gradient(180deg,#f6e8c4 0%,#e9b66a 45%,#c9822c 75%,#6b4a2a 100%)}

.box{position:absolute;left:48px;right:48px;padding:22px 34px;color:var(--ink);border-bottom:5px solid rgba(0,0,0,.12)}
.box b{font-weight:700}
.box i{font-style:italic}
.box-pleasure{top:1703px;height:145px;background:var(--green)}
.box-meaning{top:1864px;height:148px;background:var(--blue)}
.prompts{position:absolute;top:2048px;left:48px;right:48px;display:flex;justify-content:space-between}
.prompt{width:500px;text-align:center;font-weight:700;font-size:16px;line-height:1.5;padding-bottom:10px}
.prompt-a{border-bottom:3px solid var(--pink)}
.prompt-b{border-bottom:3px solid var(--green)}
.box-books{top:2143px;height:188px;background:var(--indigo);color:#fff}
.box-books h3{font-family:"Open Sans",Arial,sans-serif;font-size:28px;display:inline}
.box-books p{margin-bottom:12px}
.box-events{top:2352px;height:332px;background:var(--pink);color:#fff}
.box-events h4{font-weight:700;margin:18px 0 10px}
.box-events p{margin-bottom:8px}

.partner{position:absolute;top:2720px;left:0;right:0;display:flex;justify-content:center;align-items:center;gap:14px}
.partner-dot{width:26px;height:26px;border-radius:50%;background:var(--green)}
.partner-name{font-family:"Merriweather",Georgia,serif;font-size:28px;color:var(--green)}

.pill{position:absolute;color:#fff;font-family:"Open Sans",Arial,sans-serif;font-weight:700;text-align:center;border-radius:8px}
.pill-dates{top:2820px;left:168px;width:870px;height:42px;background:var(--green);color:var(--ink);font-size:22px;line-height:42px;transform:rotate(-1deg)}
.pill-dates em{font-style:italic}
.pill-time{top:2860px;left:485px;width:240px;height:46px;background:var(--blue);color:var(--ink);font-size:30px;line-height:46px}
.pill-place{top:2908px;left:365px;width:465px;height:44px;background:var(--purple);font-size:22px;line-height:44px}
.pill-place em{font-style:italic}

.contact{top:2978px}
.contact b{font-weight:700}
.closing{top:3030px;font-weight:700}
.footer{top:3160px;font-size:15px;line-height:1.55}
.footer a{color:var(--blue);font-weight:700}
</style>
</head>
<body>

<header class="brand" style="position:absolute">
  <span class="brand-dot"></span>
  <span class="brand-name">Step Forth Daily</span>
</header>

<section class="block intro">
  <p><strong>Hello Friends!!</strong></p>
  <p>I am excited to (hopefully) add a little love to your in-box with this newsletter. I love connecting with moms and helping them find tools to make their lives happier, more intentional, and more fun and this is a new way to do that!</p>
  <p>If you don’t know me well, I am a certified Open Horizons Trainer and I lead coaching groups for moms. My OH workshops and Empowered Moms Coaching Group have the goal of fostering connections between amazing women and empowering moms with tools to build lives they are enthusiastic about living, on purpose – and that will be the goal of this newsletter, as well!</p>
  <p>I hope you find something useful and helpful and enjoy receiving this info (and if not, feel free to unsubscribe and my feelings will not be hurt! :)!</p>
</section>

<section class="block signoff">
  <p style="margin:0">With love,</p>
  <p class="name">Dana</p>
</section>
<div class="portrait" role="img" aria-label="Photo of the coach in a blue cap with playful paint splashes"></div>

<div class="rule" style="top:996px"><span></span><span></span><span></span><span></span></div>

<div class="tips-banner" role="img" aria-label="Brush-stroke banner: Step Forth Daily Tips &amp; Tools"><span>Step Forth Daily Tips &amp; Tools:</span></div>

<section class="block happiness">
  <h2 class="section-title">Building Happiness</h2>
  <p>I firmly believe that thinking about your happiness is important and that happiness itself is a worthwhile goal! If you think about all the things you focus on in your life and all the goals you set for yourself, all of those things are leading you toward feeling happier. Happiness, in the end, is the ultimate goal.</p>
  <p>Of course, what makes each person happy is totally different – and that’s awesome and one part of what makes life fun and exciting! Many happiness experts and authors note that the key ingredieents in our lives that will make us happier are pursuing 2 categories:</p>
  <ul class="arrows">
    <li><svg width="18" height="14" viewBox="0 0 18 14"><path d="M1 7h15M10 1l6 6-6 6" fill="none" stroke="#5b2d8e" stroke-width="2"/></svg>Things that bring us pleasure (positive emotions)</li>
    <li><svg width="18" height="14" viewBox="0 0 18 14"><path d="M1 7h15M10 1l6 6-6 6" fill="none" stroke="#5b2d8e" stroke-width="2"/></svg>Things that bring us meaning &amp; fulfillment</li>
  </ul>
</section>
<div class="sunset" role="img" aria-label="Photo of hands forming a heart against a sunset"></div>

<div class="rule" style="top:1670px"><span></span><span></span><span></span><span></span></div>

<section class="box box-pleasure">
  <b>What are things that make you feel happy / provide you with pleasure (little and big things!)?</b> <i>For me: joking &amp; laughing with my kids &amp; husband, petting with my dog, sitting with a soft blanket and a book, my first sip of coffee in the morning, walking in nature, traveling, scuba diving, exercise classes, making my friends laugh.</i>
</section>
<section class="box box-meaning">
  <b>What are things that are meaningful to you / make you feel fulvilled (little and big things!)?</b> <i>For me: teaching Open Horizons workshops, spending quality time with my family, making gratitude lists, volunteering, leading moms’ coaching groups, making my kids breakfast.</i>
</section>

<div class="prompts">
  <p class="prompt prompt-a">How could you add more of those things that<br>bring you happiness to your days?</p>
  <p class="prompt prompt-b">Try to add 1 or 2 of those things per week and see<br>how your happiness increases! You are worth it!</p>
</div>

<section class="box box-books">
  <p><h3>Empowering Books</h3>: I love to read uplifting, inspiring material. Each newsletter, I’ll suggest a few books that I’ve enjoyed!</p>
  <p>The Joy Blueprint by <b><i>Marla Quinn</i></b></p>
  <p>You Are Unstoppable. How to Quit Second-Guessing Yourself and Start Loving Your Life” by <b><i>Tessa Lowell</i></b></p>
</section>

<section class="box box-events">
  <p><b>Upcoming Events:</b> I lead an Open Horizons Workshop 2-3 times per year. The next one is coming up in September/October. More details to come – but here is a little info…</p>
  <h4>Moms - Back to School, Back to You!</h4>
  <p>In September, the kids will be going back to school and you can spend time focusing on YOU. Let this be the year where you take time to focus on yourself so that you can feel amazing, focused, fulfilled, purposeful, and happier! Take the time to learn some simple tools to help you live a life you love, deliberately, instead of just juggling what comes at you and juggling your to-do list. In this workshop, you will be empowered to build a life you love.</p>
</section>

<div class="rule" style="top:2688px;height:3px"><span></span><span></span><span></span><span></span></div>

<div class="partner">
  <span class="partner-dot"></span>
  <span class="partner-name">Open Horizons</span>
</div>

<div class="pill pill-dates">Dates: 3 morning workshop - <em>SEPTEMBER 27, OCTOBER 4, OCTOBER 11</em></div>
<div class="pill pill-time">9:30 – 12:30</div>
<div class="pill pill-place">Dana’s home in <em>CEDAR RIDGE HEIGHTS</em></div>

<p class="block contact">Interested? Email me: <b>dana@stepforthdaily.example</b></p>
<p class="block closing">Enjoy the rest of Summer Break! Savor each amazing day! How can you add a little more HAPPY to your August?? Make the choice and do it!</p>

<div class="rule" style="top:3137px;height:3px"><span></span><span></span><span></span><span></span></div>

<p class="block footer">This email is sent by Brightpost Mailing Ltd on behalf of <b><i>CLIENT NAME</i></b>. We only send emails that we feel are relevant to you.<br>You can unsubscribe from future emails from this client by clicking <a href="#">here</a>.</p>

</body>
</html>
```